business card for a massage therapy practice named 'Cedar and Willow Massage Studio'

I really need a trendy, yet easy on the eyes business card to complement my logo. Ideally with some gold or rose gold foil work.

My uploaded file of the logo I have in horizontal but I have a vertical version as well. Another color that is used in the website is a blush pink here and there. I'd like to see some trendy tropical leaves in the design.

```html
<!DOCTYPE html>
<html lang="en">
<head>
<meta charset="utf-8">
<title>Cedar and Willow Massage Studio – Business Card</title>
<link rel="stylesheet" href="https://fonts.googleapis.com/css2?family=Lato:wght@300;400&display=swap">
<style>
  :root {
    --page: #e9e8e6;
    --card: #ffffff;
    --mint: #9fd0c3;
    --mint-deep: #8cc4b6;
    --ink: #1d1d1d;
    --gold: #a8925c;
    --shadow: 0 10px 28px rgba(0,0,0,.14);
  }
  * { box-sizing: border-box; margin: 0; padding: 0; }
  html, body { width: 1200px; height: 1200px; overflow: hidden; }
  body {
    background: var(--page);
    font-family: "Lato", sans-serif;
    color: var(--ink);
    position: relative;
  }
  .card {
    position: absolute;
    left: 180px;
    width: 840px;
    height: 480px;
    background: var(--card);
    box-shadow: var(--shadow);
    overflow: hidden;
  }
  .card--front { top: 80px; }
  .card--back { top: 640px; }

  /* Front */
  .brand {
    position: absolute;
    left: 50%; top: 50%;
    transform: translate(-50%, -50%);
    display: flex;
    align-items: center;
    gap: 26px;
  }
  .brand__mark {
    width: 74px; height: 74px;
    border-radius: 50%;
    background: var(--gold);
    flex: none;
  }
  .brand__name {
    font-weight: 400;
    font-size: 40px;
    line-height: 1.15;
    letter-spacing: 1px;
    color: var(--ink);
  }
  .brand__name span { display: block; font-size: 22px; letter-spacing: 6px; text-transform: uppercase; }

  /* Back */
  .holder {
    position: absolute;
    left: 370px; top: 62px;
    font-weight: 300;
    font-size: 38px;
    letter-spacing: 1px;
    text-transform: uppercase;
  }
  .band {
    position: absolute;
    left: 0; right: 0;
    top: 130px; height: 220px;
    background: var(--mint);
  }
  .seal {
    position: absolute;
    left: 20px; top: 80px;
    width: 320px; height: 320px;
    border-radius: 50%;
    background: var(--card);
    border: 16px solid var(--mint-deep);
    display: flex;
    align-items: center;
    justify-content: center;
    text-align: center;
  }
  .seal .brand__name { font-size: 28px; }
  .seal .brand__name span { font-size: 15px; letter-spacing: 4px; margin-top: 6px; }
  .contacts {
    position: absolute;
    left: 370px; top: 150px;
    list-style: none;
    color: #fff;
    font-weight: 300;
    font-size: 26px;
  }
  .contacts li {
    display: flex;
    align-items: center;
    gap: 18px;
    height: 45px;
  }
  .contacts .icon {
    width: 28px; height: 28px;
    border-radius: 50%;
    background: #fff;
    flex: none;
    display: flex; align-items: center; justify-content: center;
  }
  .website {
    position: absolute;
    left: 370px; top: 388px;
    font-weight: 400;
    font-size: 26px;
    letter-spacing: .5px;
  }
</style>
</head>
<body>

<section class="card card--front" aria-label="Card front">
  <div class="brand">
    <div class="brand__mark"></div>
    <div class="brand__name">Cedar and Willow<span>Massage Studio</span></div>
  </div>
</section>

<section class="card card--back" aria-label="Card back">
  <h1 class="holder">Marisol Ortega LMT</h1>
  <div class="band"></div>
  <div class="seal">
    <div class="brand__name">Cedar and Willow<span>Massage Studio</span></div>
  </div>
  <ul class="contacts">
    <li>
      <span class="icon">
        <svg width="16" height="16" viewBox="0 0 16 16" aria-hidden="true"><path d="M4 2 L6 5 L5 6.5 Q6.5 9.5 9.5 11 L11 10 L14 12 L12.5 14 Q6 13 2 4 Z" fill="var(--mint)"/></svg>
      </span>
      916.555.0148
    </li>
    <li>
      <span class="icon">
        <svg width="16" height="16" viewBox="0 0 16 16" aria-hidden="true"><rect x="2" y="4" width="12" height="8" fill="none" stroke="var(--mint)" stroke-width="1.6"/><path d="M2 4 L8 9 L14 4" fill="none" stroke="var(--mint)" stroke-width="1.6"/></svg>
      </span>
      cedarandwillow@gmail.com
    </li>
    <li><span class="icon"></span>@cedarandwillow</li>
    <li><span class="icon"></span>@cedarandwillow</li>
  </ul>
  <p class="website">www.cedarandwillow.com</p>
</section>

</body>
</html>
```